Day Spa Web Design Project

We just created a blog to add to our main site. We need the colors to match our main site and the look and feel of the blog to be smoother and less ameture looking, like the examples below.

Main Site, match this color scheme:
http://www.verelladayspa.com/

The project site:
http://blog.verelladayspa.com/

Our industry leaders blog site is our comparative and examples of what we need:
http://blog.wellnooklist.com/
http://blog.purelathermjournal.com/
http://thekelotabathblog.com/ (i like the layout a lot)
http://www.kneadharbor.com/blog/

Requirements
Must have
• social sharing.
Responsive design (already has it just keep it)
appealing mobile front page

```html
<!DOCTYPE html>
<html lang="en">
<head>
<meta charset="utf-8">
<title>Verella Day Spa — Blog</title>
<link href="https://fonts.googleapis.com/css2?family=Questrial&family=Arimo:wght@400;700&display=swap" rel="stylesheet">
<style>
:root{
  --dark:#1b100a;
  --dark-2:#2a1a10;
  --sand:#f3cb95;
  --sand-light:#f7dcb4;
  --brown:#6a2c0b;
  --ink:#3b2514;
  --body:#8b6b4d;
  --accent:#c5712a;
  --cream:#f6f1dd;
  --line:#d9ad78;
}
*{margin:0;padding:0;box-sizing:border-box}
html,body{width:720px;height:1200px;overflow:hidden;background:var(--sand)}
.page{position:relative;width:720px;height:1200px;background:var(--sand);font-family:"Arimo",sans-serif;color:var(--body)}
.abs{position:absolute}
.site-header{left:0;top:0;width:720px;height:59px;background:linear-gradient(#0e0805,var(--dark-2))}
.brand{left:72px;top:6px;font-family:"Questrial",sans-serif;color:#fff}
.brand-name{font-size:26px;line-height:28px}
.brand-tag{font-size:11px;letter-spacing:.3px;margin-top:1px}
.main-nav{left:464px;top:23px;font-family:"Questrial",sans-serif;font-size:9.5px;color:#fff;letter-spacing:.3px;display:flex;gap:14px}
.hero{left:0;top:59px;width:720px;height:246px;background:radial-gradient(circle at 22% 60%,#8fc23a 0,#a9cf5c 18%,transparent 40%),radial-gradient(circle at 82% 40%,#f3d1b4 0,#e9b893 22%,transparent 45%),linear-gradient(100deg,#e9efc6,#cfe08e 45%,#f0e6cf 70%,#f1d6bb)}
.hero-title{left:70px;top:142px;font-family:"Questrial",sans-serif;font-size:31px;line-height:35px;color:#111;letter-spacing:.5px}
.hero-dots{left:74px;top:287px;display:flex;gap:5px}
.hero-dots span{width:7px;height:7px;border-radius:50%;background:#ccc}
.hero-dots span:first-child{background:#333}
.crumb{left:74px;top:318px;font-size:7.5px;color:var(--ink)}
.search{left:502px;top:311px;width:145px;height:18px;background:#fff;border:2px solid var(--sand-light)}
.rule{left:72px;width:576px;border-top:1px dashed var(--line)}
.card{width:168px;text-align:center}
.card-img{width:168px;height:156px;position:relative}
.share-bar{position:absolute;left:0;top:0;width:168px;height:20px;background:rgba(255,255,255,.85);display:flex;gap:6px;align-items:center;justify-content:center;font-size:6.5px;color:var(--ink)}
.comment-tag{position:absolute;left:3px;bottom:3px;font-size:7px;font-style:italic;color:#fff}
.card-title{margin-top:11px;font-family:"Questrial",sans-serif;font-size:10.5px;color:var(--ink);letter-spacing:.3px}
.card-text{margin-top:9px;font-size:7px;line-height:10.8px;text-align:justify;text-align-last:center}
.btn{display:inline-block;margin-top:14px;width:55px;height:20px;line-height:20px;background:var(--brown);color:#fff;font-size:7.5px}
.feed-title{font-family:"Questrial",sans-serif;font-size:9.5px;color:var(--ink);letter-spacing:.3px}
.feed-btn{position:absolute;top:-3px;right:0;height:13px;padding:0 5px;background:#f0f0f0;border:1px solid #ccc;font-size:6px;line-height:11px;color:#345}
.feed-item{position:absolute;left:0;width:168px;display:flex;gap:6px;font-size:6.8px;line-height:9px}
.avatar{width:24px;height:24px;flex:none;background:linear-gradient(#e6c2a2,#8b5a3c)}
.feed-item b{font-weight:400;color:var(--accent)}
.meta{color:#a48463}
.follow{left:480px;top:966px;width:168px;text-align:center;font-family:"Questrial",sans-serif;font-size:14px;line-height:16.5px;color:var(--ink)}
.follow .or{color:var(--accent);font-size:11px}
.socials{left:501px;top:1061px;display:flex;gap:2px}
.socials span{width:19px;height:19px;border-radius:50%;background:var(--brown)}
.site-footer{left:0;top:1106px;width:720px;height:94px;background:var(--dark)}
.email-label{left:173px;top:1127px;font-family:"Questrial",sans-serif;font-size:13px;color:#fff;letter-spacing:.3px}
.email-input{left:318px;top:1124px;width:168px;height:20px;background:var(--cream)}
.submit{left:492px;top:1124px;width:53px;height:20px;background:var(--brown);color:#fff;font-size:7.5px;line-height:20px;text-align:center}
.footer-rule{left:72px;top:1160px;width:576px;border-top:1px solid #3a2a1f}
.copyright{left:0;top:1172px;width:720px;text-align:center;font-size:7px;color:#fff}
</style>
</head>
<body>
<div class="page">
  <header class="site-header abs"></header>
  <div class="brand abs"><div class="brand-name">Verella Day Spa</div><div class="brand-tag">Natural Treatments for Body, Skin &amp; Nails</div></div>
  <nav class="main-nav abs"><span>HOME</span><span>|</span><span>ABOUT US</span><span>|</span><span>CONTACT</span></nav>

  <section class="hero abs" role="img" aria-label="Spa scene with green candles, cream jar, chrysanthemums and a smiling woman holding a frangipani flower"></section>
  <h1 class="hero-title abs" style="font-weight:400">NATURAL TREATMENTS FOR<br>BODY, SKIN &amp; NAILS</h1>
  <div class="hero-dots abs"><span></span><span></span><span></span></div>

  <div class="crumb abs">HOME</div>
  <div class="search abs"></div>
  <div class="rule abs" style="top:336px"></div>

  <article class="card abs" style="left:72px;top:350px">
    <div class="card-img" role="img" aria-label="Woman relaxing during a back massage" style="background:linear-gradient(#b9a08f,#d9c2b4 60%,#eee)">
      <div class="share-bar"><span>Like</span><span>Tweet</span><span>+1</span><span>Share</span></div>
      <span class="comment-tag">Comment (4)</span>
    </div>
    <div class="card-title">KEYS TO STRESS REDUCTION</div>
    <p class="card-text">Some stress is natural, but often times stress becomes a problem when it leaves you feeling over-whelmed and out of control. Seventy seven percent of Americans report experiencing physical symptoms of stress, according to a 2012 study done by the American Wellness Council.</p>
    <span class="btn">Read More</span>
  </article>
  <article class="card abs" style="left:276px;top:350px">
    <div class="card-img" role="img" aria-label="Three models in colourful spring dresses" style="background:linear-gradient(90deg,#e88a3a,#f2b24a 33%,#d9c79a 34%,#c9a0a8 66%,#5b7f8f 67%,#d98ab4)"></div>
    <div class="card-title">WEARABLE SPRING TRENDS</div>
    <p class="card-text">Some stress is natural, but often times stress becomes a problem when it leaves you feeling over-whelmed and out of control. Seventy seven percent of Americans report experiencing physical symptoms of stress, according to a 2012 study done by the American Wellness Council.</p>
    <span class="btn">Read More</span>
  </article>
  <article class="card abs" style="left:480px;top:350px">
    <div class="card-img" role="img" aria-label="Woman resting face down on a massage table" style="background:linear-gradient(#9fb7c4,#d9b59a 55%,#e9e4dc)"></div>
    <div class="card-title">KEYS TO STRESS REDUCTION</div>
    <p class="card-text">Some stress is natural, but often times stress becomes a problem when it leaves you feeling over-whelmed and out of control. Seventy seven percent of Americans report experiencing physical symptoms of stress, according to a 2012 study done by the American Wellness Council.</p>
    <span class="btn">Read More</span>
  </article>

  <article class="card abs" style="left:72px;top:651px">
    <div class="card-img" role="img" aria-label="Woman resting on a white towel with a flower in her hair" style="background:linear-gradient(#7fb7c9,#e8c2a4 50%,#f5f5f5 75%,#2f6ea8)"></div>
    <div class="card-title">KEYS TO STRESS REDUCTION</div>
    <p class="card-text">Some stress is natural, but often times stress becomes a problem when it leaves you feeling over-whelmed and out of control. Seventy seven percent of Americans report experiencing physical symptoms of stress, according to a 2012 study done by the American Wellness Council.</p>
    <span class="btn">Read More</span>
  </article>
  <article class="card abs" style="left:276px;top:651px">
    <div class="card-img" role="img" aria-label="White candles, rolled towels and yellow orchids" style="background:linear-gradient(120deg,#e8d84a,#f4f0d8 40%,#f3ecd9 70%,#e6dce0)"></div>
    <div class="card-title">KEYS TO STRESS REDUCTION</div>
    <p class="card-text">Some stress is natural, but often times stress becomes a problem when it leaves you feeling over-whelmed and out of control. Seventy seven percent of Americans report experiencing physical symptoms of stress, according to a 2012 study done by the American Wellness Council.</p>
    <span class="btn">Read More</span>
  </article>
  <article class="card abs" style="left:480px;top:651px">
    <div class="card-img" role="img" aria-label="Woman relaxing outdoors among green plants" style="background:linear-gradient(90deg,#4f7a2e,#8fb05a 45%,#caa07f 70%,#5f4a30)"></div>
    <div class="card-title">KEYS TO STRESS REDUCTION</div>
    <p class="card-text">Some stress is natural, but often times stress becomes a problem when it leaves you feeling over-whelmed and out of control. Seventy seven percent of Americans report experiencing physical symptoms of stress, according to a 2012 study done by the American Wellness Council.</p>
    <span class="btn">Read More</span>
  </article>

  <div class="rule abs" style="top:954px"></div>

  <section class="abs" style="left:72px;top:968px;width:168px;height:120px">
    <div class="feed-title">CIRCLEBOOK FEED</div><span class="feed-btn">Like</span>
    <div class="feed-item" style="top:20px"><div class="avatar" role="img" aria-label="Profile photo"></div><div><b>lena marsh</b> Some stress is natural, but often times stress becomes a problem<br><span class="meta">2 mins ago - Reply - Like</span></div></div>
    <div class="feed-item" style="top:54px"><div class="avatar" role="img" aria-label="Profile photo"></div><div><b>lena marsh</b> Some stress is natural, but often times stress becomes a problem<br><span class="meta">2 mins ago - Reply - Like</span></div></div>
    <div class="feed-item" style="top:91px"><div class="avatar" role="img" aria-label="Profile photo"></div><div><b>lena marsh</b> Some stress is natural, but often times stress becomes a problem<br><span class="meta">2 mins ago - Reply - Like</span></div></div>
  </section>
  <section class="abs" style="left:276px;top:968px;width:168px;height:120px">
    <div class="feed-title">CHIRPER FEED</div><span class="feed-btn">Follow</span>
    <div class="feed-item" style="top:20px"><div class="avatar" role="img" aria-label="Profile photo"></div><div><b>@lena marsh</b> Some stress is natural, but often times stress becomes a problem<br><span class="meta">2 mins ago - Reply - Like</span></div></div>
    <div class="feed-item" style="top:54px"><div class="avatar" role="img" aria-label="Profile photo"></div><div><b>@lena marsh</b> Some stress is natural, but often times stress becomes a problem<br><span class="meta">2 mins ago - Reply - Like</span></div></div>
    <div class="feed-item" style="top:91px"><div class="avatar" role="img" aria-label="Profile photo"></div><div><b>@lena marsh</b> Some stress is natural, but often times stress becomes a problem<br><span class="meta">2 mins ago - Reply - Like</span></div></div>
  </section>

  <div class="follow abs">FOLLOW US<br>FOR GREAT SAVINGS<br><span class="or">OR</span><br>A CHANCE TO WIN SPA<br>TREATMENTS</div>
  <div class="socials abs"><span></span><span></span><span></span><span></span><span></span><span></span></div>

  <footer class="site-footer abs"></footer>
  <div class="email-label abs">FOLLOW US VIA EMAIL</div>
  <div class="email-input abs"></div>
  <div class="submit abs">SUBMIT</div>
  <div class="footer-rule abs"></div>
  <div class="copyright abs">© 2013 - VERELLA DAY SPA – TIPS N' TRICKS</div>
</div>
</body>
</html>
```